Brantor Works Business Card

Modern and Professional Business Card for a Med size construction/development company.

See the samples below for the design I like … but I need ideas for incorporating the red company logo while still keeping the clean look of the card samples that are attached.

Logo and tag line on the back … info on the front.

Tagline: Quality Starts from the Ground Up

Target Market(s)

Med-Large General Contractors

Contact Information for Business Card

Brantor Works Limited
42 Fenwick Avenue
Mt. Pearl, NL
A1N 4R9

t: 709-555-0147
f: 709-555-0182
w: www.brantorworks-example.com

Font styles to use
Sans Serif

Colors
fbee3e

Requirements
Must have
• I like the black and yellow designs of the attached samples …. but I'm not sure how to incorporate the red Brantor Works logo into that design??
Nice to have
• Construction safety strips

```html
<!DOCTYPE html>
<html lang="en">
<head>
<meta charset="utf-8">
<title>Brantor Works Business Card</title>
<link href="https://fonts.googleapis.com/css2?family=Lato:wght@400;700;900&display=swap" rel="stylesheet">
<style>
  :root {
    --stage: #2a2a2c;
    --brand-red: #ed2128;
    --card-black: #0b0b0c;
    --ink: #111111;
    --paper: #ffffff;
    --rule-front: rgba(80, 40, 30, 0.55);
    --rule-back: #555558;
  }
  html, body {
    margin: 0;
    padding: 0;
    width: 1200px;
    height: 1108px;
    overflow: hidden;
    background: var(--stage);
    font-family: "Lato", Arial, sans-serif;
  }
  .stage {
    position: relative;
    width: 1200px;
    height: 1108px;
  }
  .card {
    position: absolute;
    top: 170px;
    width: 430px;
    height: 752px;
    border-radius: 22px;
    box-shadow: 0 14px 30px rgba(0,0,0,0.45);
    overflow: hidden;
    box-sizing: border-box;
  }
  /* Front */
  .card-front {
    left: 110px;
    background: var(--brand-red);
    text-align: center;
    color: var(--paper);
  }
  .wordmark {
    position: absolute;
    top: 120px;
    left: 0;
    right: 0;
    font-weight: 900;
    font-size: 50px;
    letter-spacing: 1px;
    line-height: 1;
    color: var(--ink);
  }
  .wordmark-sub {
    display: block;
    margin-top: 10px;
    font-size: 24px;
    letter-spacing: 4px;
  }
  .person {
    position: absolute;
    top: 372px;
    left: 0;
    right: 0;
  }
  .person-name {
    margin: 0;
    font-weight: 900;
    font-size: 34px;
    letter-spacing: 1px;
    color: var(--ink);
  }
  .person-role {
    margin: 6px 0 0;
    font-size: 22px;
    color: var(--ink);
  }
  .contact-divider {
    position: relative;
    width: 250px;
    height: 30px;
    margin: 16px auto 8px;
  }
  .contact-divider::before {
    content: "";
    position: absolute;
    left: 0; right: 0; top: 15px;
    border-top: 1px solid var(--rule-front);
  }
  .contact-icons {
    position: relative;
    display: inline-flex;
    gap: 4px;
    background: var(--brand-red);
    padding: 0 6px;
  }
  .contact-icons svg { width: 28px; height: 28px; display: block; }
  .contact-list {
    margin: 0;
    padding: 0;
    list-style: none;
    font-size: 22px;
    line-height: 34px;
  }
  .rule {
    width: 260px;
    margin: 14px auto;
    border: 0;
    border-top: 1px solid var(--rule-front);
  }
  .address {
    font-style: normal;
    font-size: 22px;
    line-height: 30px;
  }
  /* Back */
  .card-back {
    left: 660px;
    background: var(--card-black);
  }
  .tread-area {
    position: absolute;
    inset: 0 0 220px 0;
    background: linear-gradient(180deg, #1b1b1d 0%, #111113 60%, var(--card-black) 100%);
  }
  .back-brand {
    position: absolute;
    left: 0; right: 0;
    bottom: 96px;
    text-align: center;
  }
  .back-wordmark {
    margin: 0;
    font-weight: 900;
    font-size: 64px;
    letter-spacing: 2px;
    line-height: 1;
    color: var(--brand-red);
  }
  .back-rule {
    width: 330px;
    margin: 14px auto 12px;
    border: 0;
    border-top: 1px solid var(--rule-back);
  }
  .tagline {
    margin: 0;
    font-size: 15px;
    letter-spacing: 1.5px;
    text-transform: uppercase;
    color: var(--paper);
  }
</style>
</head>
<body>
<main class="stage">
  <section class="card card-front" aria-label="Card front">
    <div class="wordmark">BRANTOR<span class="wordmark-sub">WORKS LIMITED</span></div>

    <div class="person">
      <h1 class="person-name">DANIEL HALE</h1>
      <p class="person-role">Founder &amp; CEO</p>

      <div class="contact-divider">
        <div class="contact-icons">
          <svg viewBox="0 0 28 28" aria-label="Phone"><circle cx="14" cy="14" r="13" fill="#111"/><path d="M9 8c1-1 2 0 3 2s0 2-1 3c1 2 2 3 4 4 1-1 1-2 3-1s3 2 2 3c-2 3-6 1-9-2s-4-7-2-9z" fill="#ed2128"/></svg>
          <svg viewBox="0 0 28 28" aria-label="Fax"><circle cx="14" cy="14" r="13" fill="#111"/><rect x="10" y="7" width="8" height="5" fill="#ed2128"/><rect x="7" y="12" width="14" height="7" rx="1" fill="#ed2128"/><rect x="10" y="16" width="8" height="5" fill="#ed2128" stroke="#111" stroke-width="1"/></svg>
          <svg viewBox="0 0 28 28" aria-label="Web"><circle cx="14" cy="14" r="13" fill="#111"/><g fill="none" stroke="#ed2128" stroke-width="1.4"><circle cx="14" cy="14" r="7.5"/><ellipse cx="14" cy="14" rx="3.5" ry="7.5"/><path d="M6.5 14h15M8 10h12M8 18h12"/></g></svg>
        </div>
      </div>

      <ul class="contact-list">
        <li>709-555-0147</li>
        <li>709-555-0182</li>
        <li>www.brantorworks-example.com</li>
      </ul>

      <hr class="rule">

      <address class="address">
        Brantor Works Limited<br>
        42 Fenwick Avenue<br>
        Port Elmsby, NL A0X 2B7
      </address>
    </div>
  </section>

  <section class="card card-back" aria-label="Card back">
    <div class="tread-area" role="img" aria-label="Faint tyre tread pattern across the card"></div>
    <div class="back-brand">
      <p class="back-wordmark">BRANTOR</p>
      <hr class="back-rule">
      <p class="tagline">Quality starts from the ground up</p>
    </div>
  </section>
</main>
</body>
</html>
```